Brimsett Gardening Fresh New Website

We are looking to create a simple fresh website for our landscaping business. The website should appeal to a 'high end' audience. We deal with a lot of Embassies and affluent clients who have extremely large gardens that are meticulously maintained. The site is about communicating our excellent landscaping and customer service skills and encouraging new clients to reach out and engage us to take care of their gardens.

The website is basically going to be our business card, it will have almost no functionality other than two 'contact us' forms, one for smaller clients and one for more detailed projects.

The website will not have a lot of written content and will have to show photos of beautifully landscaped gardens.

The main logo in black will influence the site, however, we are open to all suggestions.

We are expecting to have the following pages:
Home Page
Services
About Us
Contact Us
Showcase (photo gallery of our work)

We need someone who can code it to wordpress and be available for minor changes over a number of days. They will be simple tweaks.

```html
<!DOCTYPE html>
<html lang="en">
<head>
<meta charset="utf-8">
<title>Brimsett Gardening</title>
<link href="https://fonts.googleapis.com/css2?family=Montserrat:wght@400;500;600;700&display=swap" rel="stylesheet">
<style>
:root{
  --gold:#a06f28;
  --gold-light:#c4923f;
  --ink:#1d1d1b;
  --dark:#1a1a12;
  --panel:#232318;
  --white:#ffffff;
  --line:#8d8d8d;
  --grey:#ecebea;
  --text:#222222;
}
*{box-sizing:border-box;margin:0;padding:0}
html,body{width:1200px;height:3576px;overflow:hidden}
body{position:relative;font-family:'Montserrat',sans-serif;color:var(--text);background:var(--white)}
.abs{position:absolute}
.photo{position:absolute}
.hero{left:0;top:0;width:1200px;height:680px;background:linear-gradient(160deg,#3b4a2a 0%,#4f6b2c 35%,#6d6a5c 60%,#3e3a33 100%)}
.hero-shade{left:0;top:0;width:1200px;height:680px;background:linear-gradient(180deg,rgba(0,0,0,.45),rgba(0,0,0,.15) 40%,rgba(0,0,0,.25))}
.topbar{top:16px;left:0;width:1200px;display:flex;justify-content:center;gap:110px;color:var(--white);font-size:17px}
.topbar span{display:flex;align-items:center;gap:14px}
.nav{left:62px;top:58px;width:1077px;height:95px;background:var(--gold)}
.nav-logo{left:62px;top:58px;width:275px;height:95px;background:var(--ink);clip-path:polygon(0 0,100% 0,75% 100%,0 100%);display:flex;align-items:center;padding-left:50px}
.brand{color:var(--gold-light);font-weight:500;letter-spacing:3px;font-size:15px;line-height:1.3;display:flex;flex-direction:column;align-items:center;text-align:center}
.brand small{display:block;font-size:8px;letter-spacing:4px}
.menu{left:371px;top:58px;height:95px;display:flex;align-items:center;gap:37px;color:var(--white);font-weight:500;font-size:16px}
.search{left:1064px;top:98px}
.welcome{top:275px;width:1200px;text-align:center;color:var(--white);font-weight:600;font-size:38px}
.title{top:345px;width:1200px;text-align:center;color:var(--white);font-weight:700;font-size:66px;letter-spacing:1px}
.band-white{left:0;top:680px;width:1200px;height:1780px;background:var(--white)}
.card{left:111px;top:567px;width:977px;height:430px;background:var(--white);border-radius:26px;box-shadow:0 2px 10px rgba(0,0,0,.25)}
h2{font-weight:600;color:var(--gold);font-size:34px}
.field{position:absolute;border:1.4px solid var(--line);border-radius:7px;height:57px}
.field span{position:absolute;top:-11px;left:30px;background:var(--white);padding:0 9px;font-size:16px;font-weight:500;color:#333}
.btn{position:absolute;background:var(--gold);color:var(--white);border-radius:30px;font-weight:600;font-size:18px;display:flex;align-items:center;justify-content:center}
.about-sub{left:111px;top:1178px;font-size:24px;font-weight:500;line-height:46px;color:var(--text)}
.about-text{left:474px;top:1107px;width:610px;font-size:16px;line-height:34px}
.badge{border-radius:50%;background:var(--ink);border:3px solid #111;outline:2px dashed #8a7a5a;outline-offset:-9px;display:flex;align-items:center;justify-content:center;color:var(--gold-light);font-size:10px;letter-spacing:2px;font-weight:500;text-align:center}
.svc{position:absolute;width:412px;height:198px;border-radius:6px;overflow:hidden;border:1px solid #ddd;background:var(--grey)}
.svc .img{position:absolute;left:61px;top:0;right:0;bottom:0}
.svc .ico{position:absolute;left:29px;top:67px;width:64px;height:64px;border-radius:50%;background:var(--gold);display:flex;align-items:center;justify-content:center}
.svc .cap{position:absolute;left:127px;top:30px;color:var(--white)}
.svc .cap b{font-weight:600;font-size:22px}
.svc .cap p{font-size:16px;line-height:34px;margin-top:6px;width:270px}
.projects{left:0;top:2461px;width:1200px;height:623px;background:linear-gradient(180deg,#1f2a17,#33461f 55%,#2c3b1b)}
.proj{position:absolute;top:2720px;height:272px;border-radius:26px}
.footer{left:0;top:3084px;width:1200px;height:492px;background:linear-gradient(180deg,#1b1b12,#26261a)}
.fpanel{left:125px;top:3142px;width:483px;height:434px;background:var(--panel);border-radius:26px 26px 0 0}
.ffield{position:absolute;border:1px solid #aaa;border-radius:4px;height:40px}
.ffield span{position:absolute;top:-8px;left:20px;background:var(--panel);padding:0 6px;font-size:11px;font-weight:600;color:var(--white)}
.flinks{left:585px;width:600px;color:var(--white);font-size:16px;font-weight:500;text-align:center}
.social{display:flex;gap:7px}
.social i{width:31px;height:31px;border:1.5px solid var(--white);border-radius:50%;display:block}
</style>
</head>
<body>
<div class="photo hero" role="img" aria-label="Manicured lawn with a curved brick garden path"></div>
<div class="abs hero-shade"></div>

<div class="abs topbar">
  <span><svg width="16" height="20" viewBox="0 0 16 20"><path d="M8 0a8 8 0 0 0-8 8c0 6 8 12 8 12s8-6 8-12a8 8 0 0 0-8-8zm0 11a3 3 0 1 1 0-6 3 3 0 0 1 0 6z" fill="#fff"/></svg>BRIMSETT GARDENING, ALDERWOOD LANE 14, 091 872</span>
  <span><svg width="15" height="15" viewBox="0 0 24 24"><path d="M6.6 10.8a15 15 0 0 0 6.6 6.6l2.2-2.2c.3-.3.7-.4 1-.2 1.1.4 2.3.6 3.6.6.6 0 1 .4 1 1V20c0 .6-.4 1-1 1A17 17 0 0 1 3 4c0-.6.4-1 1-1h3.5c.6 0 1 .4 1 1 0 1.3.2 2.5.6 3.6.1.3 0 .7-.2 1z" fill="#fff"/></svg>+1 555 014 2290</span>
</div>

<div class="abs nav"></div>
<div class="abs nav-logo">
  <div class="brand">BRIMSETT<small>GARDENING</small></div>
</div>
<nav class="abs menu"><span>HOME</span><span>OUR SERVICES</span><span>ABOUT US</span><span>GALLERY</span><span>CONTACT US</span></nav>
<svg class="abs search" width="16" height="16" viewBox="0 0 16 16"><circle cx="6.5" cy="6.5" r="5" stroke="#fff" stroke-width="2.2" fill="none"/><path d="M10 10l5 5" stroke="#fff" stroke-width="2.4"/></svg>

<div class="abs welcome">WELCOME TO</div>
<div class="abs title">BRIMSETT GARDENING</div>

<div class="abs band-white"></div>

<section class="abs card">
  <h2 style="position:absolute;top:48px;width:100%;text-align:center">MEET OUR CLIENTS</h2>
  <div class="field" style="left:11px;top:139px;width:313px"><span>NAME</span></div>
  <div class="field" style="left:331px;top:139px;width:315px"><span>EMAIL</span></div>
  <div class="field" style="left:653px;top:139px;width:314px"><span>COMPANY NAME</span></div>
  <div class="field" style="left:11px;top:223px;width:313px"><span>COUNTRY</span></div>
  <div class="field" style="left:331px;top:223px;width:315px"><span>CITY</span></div>
  <div class="field" style="left:653px;top:223px;width:314px"><span>INDUSTRY TYPE</span></div>
  <div class="field" style="left:11px;top:308px;width:313px"><span>SERVICE</span></div>
  <div class="field" style="left:331px;top:308px;width:636px"><span>MESSAGE</span></div>
</section>
<div class="btn" style="left:515px;top:974px;width:168px;height:47px">OUR CLIENTS</div>

<h2 class="abs" style="left:114px;top:1104px">ABOUT US</h2>
<div class="abs about-sub">THE BEST CHOICE FOR<br>GARDENING</div>
<div class="btn" style="left:115px;top:1306px;width:169px;height:45px">LEARN MORE</div>
<div class="photo" role="img" aria-label="Line drawing of a leaf" style="left:132px;top:1396px;width:239px;height:257px;background:radial-gradient(ellipse at center,#eeeeee 0%,#ffffff 70%)"></div>
<p class="abs about-text">Lorem ipsum dolor sit amet, consectetur adipiscing elit, sed do eiusmod tempor incididunt ut labore et dolore magna aliqua. Ut enim ad minim veniam, quis nostrud exercitation.</p>
<div class="photo" role="img" aria-label="Lawn bordered by hedges and flowering shrubs" style="left:474px;top:1239px;width:298px;height:414px;background:linear-gradient(180deg,#3f6a2a,#6aa33a 55%,#9ac95a 85%,#d8d8cc)"></div>
<div class="photo" role="img" aria-label="Aerial view of a winding gravel path and a gardener mowing" style="left:789px;top:1239px;width:299px;height:414px;border-radius:0 0 40px 0;background:linear-gradient(135deg,#5c9a32,#7db943 50%,#4f8a2b)"></div>
<div class="abs badge" style="left:716px;top:1382px;width:130px;height:130px">BRIMSETT<br>GARDENING</div>

<h2 class="abs" style="top:1739px;width:1200px;text-align:center">OUR SERVICES</h2>
<div class="svc" style="left:171px;top:1842px">
  <div class="img" role="img" aria-label="Lakeside estate garden" style="background:linear-gradient(180deg,#5d6f80,#3e5a3a 60%,#2f4a22)"></div>
  <div class="ico"><svg width="36" height="36" viewBox="0 0 36 36" fill="none" stroke="#fff" stroke-width="1.6"><circle cx="13" cy="14" r="8"/><circle cx="24" cy="17" r="7"/><path d="M13 22v10M24 24v8M6 32h24"/></svg></div>
  <div class="cap"><b>LOREM IPSUM</b><p>Lorem ipsum dolor sit amet, consectetur adipiscing elit, sed do eiusmod.</p></div>
</div>
<div class="svc" style="left:617px;top:1842px">
  <div class="img" role="img" aria-label="Freshly mown lawn with flower border" style="background:linear-gradient(180deg,#3e5e2a,#6fb23a 35%,#5aa02c)"></div>
  <div class="ico"><svg width="36" height="36" viewBox="0 0 36 36" fill="none" stroke="#fff" stroke-width="1.6"><path d="M26 4v14M22 18h8l-1 12h-6zM10 30V18M10 18c-5 0-6-5-6-5s5-1 6 5c1-6 6-5 6-5s-1 5-6 5M4 32h28"/></svg></div>
</div>
<div class="svc" style="left:171px;top:2074px">
  <div class="img" role="img" aria-label="Park with trees and flower beds" style="background:linear-gradient(180deg,#3c7fd0,#7fb1e6 30%,#2f5a28 55%,#6aa83a)"></div>
  <div class="ico"><svg width="36" height="36" viewBox="0 0 36 36" fill="none" stroke="#fff" stroke-width="1.6"><path d="M18 33V12M18 12c-6 0-8-7-8-7s7 0 8 7c1-7 8-7 8-7s-2 7-8 7M18 22c-6 0-8-5-8-5s6-1 8 5M18 22c6 0 8-5 8-5s-6-1-8 5"/></svg></div>
</div>
<div class="svc" style="left:617px;top:2074px">
  <div class="img" role="img" aria-label="Garden path with flowering beds and pergola" style="background:linear-gradient(180deg,#dfe4ea,#5a7d3a 40%,#7a6aa8 65%,#5aa02c)"></div>
  <div class="ico"><svg width="36" height="36" viewBox="0 0 36 36" fill="none" stroke="#fff" stroke-width="1.6"><circle cx="12" cy="10" r="5"/><circle cx="24" cy="12" r="5"/><path d="M12 15v17M24 17v15M5 32h26"/></svg></div>
</div>
<div class="btn" style="left:485px;top:2320px;width:229px;height:45px">VIEW ALL SERVICES</div>

<div class="photo projects" role="img" aria-label="Dark green estate lawn surrounded by trees"></div>
<h2 class="abs" style="top:2567px;width:1200px;text-align:center;color:var(--white)">OUR PROJECTS</h2>
<div class="proj" role="img" aria-label="Open parkland under blue sky" style="left:-40px;width:130px;background:linear-gradient(180deg,#8fc0ea,#6f9a4a 60%,#8ab54a)"></div>
<div class="proj" role="img" aria-label="Curved lawn edged with shrubs and gravel" style="left:101px;width:325px;background:linear-gradient(135deg,#2e5a2a,#7cbf3c 60%,#c9c2b4)"></div>
<div class="proj" role="img" aria-label="Raised planting bed by a stone wall" style="left:437px;width:325px;background:linear-gradient(180deg,#c7d6e6,#6a6a62 40%,#3a7a2c 70%,#8c8c8a)"></div>
<div class="proj" role="img" aria-label="Gardener trimming hedges" style="left:774px;width:325px;background:linear-gradient(135deg,#c9c24a,#6a8e2c 45%,#2f5a22)"></div>
<div class="proj" role="img" aria-label="Flowering shrubs" style="left:1110px;width:130px;background:linear-gradient(180deg,#6a8e3a,#4a6a2a)"></div>

<div class="photo footer" role="img" aria-label="Dark garden backdrop"></div>
<section class="abs fpanel">
  <div style="position:absolute;top:36px;width:100%;text-align:center;color:var(--white);font-weight:600;font-size:28px">OUR PROJECTS</div>
  <div class="ffield" style="left:11px;top:114px;width:225px"><span>NAME</span></div>
  <div class="ffield" style="left:246px;top:114px;width:226px"><span>EMAIL</span></div>
  <div class="ffield" style="left:11px;top:174px;width:225px"><span>PHONE</span></div>
  <div class="ffield" style="left:246px;top:174px;width:226px"><span>PROJECTS</span></div>
  <div class="ffield" style="left:11px;top:235px;width:461px"><span>MESSAGE</span></div>
</section>
<div class="btn" style="left:282px;top:3449px;width:168px;height:47px">SUBMIT NOW</div>

<div class="abs" style="left:785px;top:3228px;width:200px;display:flex;justify-content:center">
  <div class="brand" style="font-size:17px">BRIMSETT<small style="font-size:10px">GARDENING</small></div>
</div>
<div class="abs flinks" style="top:3304px">HOME &nbsp;&nbsp;&nbsp;|&nbsp;&nbsp;&nbsp; OUR SERVICES &nbsp;&nbsp;&nbsp;|&nbsp;&nbsp;&nbsp; ABOUT US</div>
<div class="abs flinks" style="top:3350px">GALLERY &nbsp;&nbsp;&nbsp;|&nbsp;&nbsp;&nbsp; CONTACT US</div>
<div class="abs social" style="left:817px;top:3405px"><i></i><i></i><i></i><i></i></div>
<div class="abs flinks" style="top:3471px;font-size:12px">©2024 COPYRIGHTS &nbsp;&nbsp;&nbsp;|&nbsp;&nbsp;&nbsp; ALL RIGHTS RESERVED</div>
</body>
</html>
```